Tolbek cards

I want a simple business card that pops.
Logo on one side.
On side two i want.
"Are you thinking about a new building on your property, or renovating an existing structure? Contact".....
Owners Name: Dale Whitacre
Owners Phone number: 610-555-0187
Address:4076 Copper Ridge RD, Alder Bend, OR 97999
Committed to Quality, Service, and Integrity

```html
<!DOCTYPE html>
<html lang="en">
<head>
<meta charset="utf-8">
<title>Tolbek Builders LLC – Business Cards</title>
<link href="https://fonts.googleapis.com/css2?family=Roboto:wght@400;700;900&family=Roboto+Condensed:wght@700&display=swap" rel="stylesheet">
<style>
  :root{
    --backdrop:#2a2a2a;
    --brown-dark:#4b3120;
    --brown-deep:#5c3f28;
    --brown-light:#9d8569;
    --tan:#a48c72;
    --tan-text:#a08466;
    --paper:#f1efeb;
    --ink:#2e2119;
    --white:#ffffff;
    --cream:#ece6df;
  }
  *{margin:0;padding:0;box-sizing:border-box}
  html,body{width:1200px;height:576px;overflow:hidden;background:var(--backdrop)}
  body{position:relative;font-family:"Roboto",Arial,sans-serif}
  .card{position:absolute;top:139px;height:293px;border-radius:10px;overflow:hidden}

  /* Front */
  .card--front{left:102px;width:484px;background:linear-gradient(180deg,var(--brown-light) 0%,var(--brown-deep) 100%)}
  .front-brand{position:absolute;left:0;right:0;top:52px;text-align:center;color:var(--cream);font-weight:900}
  .front-brand__mark{display:block;width:60px;height:60px;margin:0 auto 14px;background:var(--cream)}
  .front-brand__name{display:block;font-size:52px;line-height:48px;letter-spacing:1px}
  .front-brand__sub{display:block;font-size:16px;letter-spacing:2.5px;margin-top:4px}
  .front-tagline{position:absolute;left:0;right:0;top:254px;display:flex;align-items:center;justify-content:center;gap:10px;color:var(--cream);font-size:13px}
  .front-tagline::before,.front-tagline::after{content:"";width:68px;height:1px;background:var(--cream);opacity:.8}

  /* Back */
  .card--back{left:596px;width:480px;background:var(--paper)}
  .back-panel{position:absolute;left:0;top:0;width:104px;height:100%;background:var(--brown-dark)}
  .back-brand{position:absolute;right:14px;top:26px;text-align:center;color:var(--brown-dark);font-weight:900}
  .back-brand__name{display:block;font-size:42px;line-height:38px;letter-spacing:1px}
  .back-brand__sub{display:block;font-size:12px;letter-spacing:3px;margin-top:2px}
  .back-band{position:absolute;left:116px;right:0;top:97px;height:52px;background:var(--tan);color:var(--white);
    font-family:"Roboto Condensed","Arial Narrow",sans-serif;font-weight:700;font-size:12.5px;line-height:16px;
    text-align:right;padding:8px 15px 0 0;text-transform:uppercase}
  .back-contact-pill{position:absolute;right:15px;top:142px;width:82px;height:17px;border-radius:9px;background:var(--brown-dark);
    color:var(--white);font-family:"Roboto Condensed","Arial Narrow",sans-serif;font-weight:700;font-size:11.5px;line-height:17px;text-align:center}
  .back-details{position:absolute;right:15px;top:168px;text-align:right}
  .owner-name{font-size:21px;font-weight:700;color:var(--ink);text-transform:uppercase;letter-spacing:.3px}
  .owner-name span{color:var(--tan-text)}
  .owner-phone{font-size:13px;font-weight:700;color:var(--ink);margin-top:3px}
  .owner-address{font-size:12px;color:var(--tan-text);margin-top:4px}
  .back-rule{position:absolute;left:188px;right:15px;top:243px;height:1px;background:var(--tan-text);opacity:.7}
  .back-tagline{position:absolute;right:15px;top:255px;font-size:13px;color:var(--ink)}
</style>
</head>
<body>
  <section class="card card--front" aria-label="Card front">
    <div class="front-brand">
      <span class="front-brand__mark"></span>
      <span class="front-brand__name">TOLBEK</span>
      <span class="front-brand__sub">BUILDERS LLC</span>
    </div>
    <p class="front-tagline">Committed to Quality, Service &amp; Integrity</p>
  </section>

  <section class="card card--back" aria-label="Card back">
    <div class="back-panel" role="img" aria-label="Large brown brand decoration"></div>
    <div class="back-brand">
      <span class="back-brand__name">TOLBEK</span>
      <span class="back-brand__sub">BUILDERS LLC</span>
    </div>
    <p class="back-band">Are you thinking about a new building on your<br>property, or renovating an existing structure?</p>
    <p class="back-contact-pill">CONTACT</p>
    <div class="back-details">
      <p class="owner-name">Dale <span>Whitacre</span></p>
      <p class="owner-phone">Call: 610-555-0187</p>
      <p class="owner-address">Add.: 4076 Copper Ridge RD, Alder Bend, OR 97999</p>
    </div>
    <div class="back-rule"></div>
    <p class="back-tagline">Committed to Quality, Service &amp; Integrity</p>
  </section>
</body>
</html>
```